One of Australia's fastest growing energy maintenance contractors needs a new website

www.brightleaf.com.au
Our business has evolved over the past years and now our website is no longer relevant.
We clean solar panels and we vacuum roof gutters.
We clean solar panels on the roofs of residential houses right up to billion dollar solar farms with in excess of 1 million panels. We offer thermal image testing and bird proofing for our residential and commercial clients and thermal drone imaging services for our solar farm clients.
We vacuum clean roof gutters (using a LoftSuck) on the residential house next door right up to enormous private and public schools, colleges, shopping centres, strat complexes and commercial buildings.
When first built our business had more of a domestic residential skew and the website reflected that. While that is still part of our core business we are now bidding on and have secured large government, commercial and infrastructure contracts and our new website needs to reflect our growth and our new business. We need a new site that it optimised for both desktop ad phone viewing as our latest figures showed that 73% of people visiting our site are on mobile phones. We have an extensive amount of data on Tallymark Insights available as well as Bidlines. Both that would also need integrating with the site along with a few other plugins such as Quilro Chat IQ, Chatterbox etc along with SEO key words etc. We are also the winner and finalists over multiple years of the small business of the year awards and we like to proudly and prominently display those on our site.
We are looking for a new site with a modern professional feel / theme
There is a definitive break in our business between the solar Panel cleaning clients and the gutter cleaning clients so we would like a home page that begins with a simple choice:
Solar Panel Cleaning – Gutter Cleaning
With a professional full screen background image (we have hundreds to choose from) and along the bottom a small area with rights reserved etc, phone number etc (at some point in the future we will split these into two businesses but for now it’s what we have).
After that selection is made we would like a repeat of that same scenario but the selection is:
If it’s Solar Panel Cleaning
(new background image)
Government – Infrastructure – Commercial – Residential
If it’s Gutter Cleaning
(new background image)
Government – Strata – Commercial – Residential
After making those choices then onto the relevant pages with background images relevant to each sector and a them that suits (on the residential we would like to keep the link to our tallymark reviews) - We will provide copy / text for each relevant page.
Other than that, a menu inclusive of the above and:
Resellers Portal – we will provide a link to this from Quilro CRM)
Customer portal (we will supply a link to this from our booking system)
We also need a page for our Solar Resellers / Partners page but we will give them a link to this, it won’t be listed on the site.
Request a quote page (Again we will provide information from Quilro as this will be linked to the CRM)
Standard contact us page inclusive of phone numbers, address and fields supplied from CRM
Sydney – 02 7391 8056
Southern Highlands – 02 4863 1708
Goulburn – 02 4863 1708
Canberra – 02 6172 4385
Wollongong – 02 4239 5817
sales@brightleaf.com.au
Head Office - Fernbrook NSW 2584
ABN: 48093716552
Responsive Design: Optimized for desktop and mobile (73% mobile visitors).
Fast Loading Speed: Optimized for performance.
Smooth Transition Animations: For service and category selection.
Sticky Contact Bar: Always accessible at the bottom of mobile screens for quick calls.
SEO Optimization: Focused on government tenders, large-scale commercial contracts, and infrastructure projects.
Integrations
Tallymark Insights & Tallymark Bidlines.
Quilro Chat IQ.
Chatterbox Beacon.
SEO tools and keyword optimization.
Many many more images available if needed
Target Market(s)
Residential, commercial, Government

```html
<!DOCTYPE html>
<html lang="en">
<head>
<meta charset="utf-8">
<title>Brightleaf – Website Home Screens</title>
<link rel="stylesheet" href="https://fonts.googleapis.com/css2?family=Lexend:wght@300;400;500&display=swap">
<style>
  :root {
    --stage: #424242;
    --brand-blue: #0a67b1;
    --button-blue: #1a7fc0;
    --white: #ffffff;
    --ink: #333333;
    --overlay: rgba(38, 38, 42, 0.82);
    --rule: rgba(255, 255, 255, 0.85);
  }
  * { box-sizing: border-box; margin: 0; padding: 0; }
  html, body { width: 1200px; height: 314px; overflow: hidden; }
  body {
    background: var(--stage);
    font-family: "Lexend", sans-serif;
    position: relative;
  }
  .screen {
    position: absolute;
    top: 21px;
    width: 359px;
    height: 272px;
    background: var(--white);
    overflow: hidden;
  }
  .screen--home { left: 27.5px; }
  .screen--solar { left: 420.5px; }
  .screen--gutter { left: 813.5px; }

  /* Header */
  .site-header {
    height: 27px;
    position: relative;
    background: var(--white);
  }
  .brand {
    position: absolute;
    left: 33px;
    top: 8px;
    display: flex;
    align-items: center;
    gap: 3px;
    color: var(--brand-blue);
    font-weight: 500;
    font-size: 7.5px;
  }
  .brand__mark {
    width: 10px;
    height: 10px;
    background: var(--brand-blue);
  }
  .portal-link {
    position: absolute;
    top: 7px;
    height: 13px;
    border: 0.6px solid #888;
    border-radius: 1.5px;
    font-size: 5.2px;
    color: var(--ink);
    display: flex;
    align-items: center;
    justify-content: center;
    white-space: nowrap;
  }
  .portal-link--resellers { left: 199px; width: 49px; }
  .portal-link--customer { left: 254px; width: 50px; }
  .menu-toggle { position: absolute; left: 314px; top: 9px; }

  /* Hero */
  .hero {
    position: relative;
    height: 171px;
  }
  .hero__photo { position: absolute; inset: 0; }
  .hero__photo--split {
    background:
      linear-gradient(155deg, #4d6fa8 0%, #9fb0c8 38%, #c9c7c0 50%, #9a8f86 62%, #3d66c4 80%, #c8a04a 100%);
  }
  .hero__photo--panels {
    background: linear-gradient(160deg, #a9b6cf 0%, #3d5aa0 40%, #2f4a8f 70%, #5f6fa5 100%);
  }
  .hero__photo--gutter {
    background: linear-gradient(150deg, #b8b8b8 0%, #8e8e8e 35%, #c7b9a4 60%, #5a6f9a 80%, #3a3a3a 100%);
  }
  .hero__panel {
    position: absolute;
    left: 42px;
    top: 47.5px;
    width: 280px;
    height: 74px;
    background: var(--overlay);
    border-radius: 7px;
    color: var(--white);
    text-align: center;
  }
  .hero__title {
    font-weight: 500;
    font-size: 11.6px;
    letter-spacing: 0.1px;
    white-space: nowrap;
  }
  .screen--home .hero__title { margin-top: 14px; }
  .screen--solar .hero__title,
  .screen--gutter .hero__title { margin-top: 24px; }
  .hero__sectors {
    margin-top: 5px;
    font-weight: 500;
    font-size: 6.4px;
    white-space: nowrap;
  }
  .hero__choices {
    margin-top: 10px;
    display: flex;
    justify-content: center;
    gap: 11px;
  }
  .choice {
    width: 74px;
    height: 13px;
    font-size: 5.3px;
    display: flex;
    align-items: center;
    justify-content: center;
    border-radius: 1px;
    color: var(--white);
  }
  .choice--solar { background: var(--button-blue); }
  .choice--gutter { border: 0.7px solid var(--white); }

  /* Footer */
  .site-footer {
    height: 74px;
    background: var(--brand-blue);
    color: var(--white);
    position: relative;
  }
  .footer-brand {
    position: absolute;
    left: 0;
    width: 106px;
    top: 20px;
    display: flex;
    flex-direction: column;
    align-items: center;
    gap: 6px;
  }
  .footer-brand__mark { width: 20px; height: 20px; background: var(--white); }
  .footer-brand__name { font-weight: 500; font-size: 10px; }
  .footer-rule {
    position: absolute;
    top: 19px;
    height: 40px;
    width: 0.8px;
    background: var(--rule);
  }
  .footer-rule--one { left: 106px; }
  .footer-rule--two { left: 225px; }
  .footer-col { position: absolute; top: 12px; }
  .footer-col--locations { left: 121px; }
  .footer-col--company { left: 241px; }
  .footer-col__heading { font-weight: 400; font-size: 6.6px; margin-bottom: 5px; }
  .footer-list { list-style: none; font-weight: 300; font-size: 4.5px; white-space: nowrap; }
  .footer-list li { display: flex; align-items: center; gap: 4px; height: 7.2px; }
  .footer-list svg { flex: none; }
  .footer-list--company li { align-items: flex-start; height: auto; margin-bottom: 4px; }
  .copyright { position: absolute; left: 242px; top: 58px; font-weight: 300; font-size: 4.5px; }
</style>
</head>
<body>

<!-- Screen 1: service choice -->
<section class="screen screen--home">
  <header class="site-header">
    <div class="brand"><span class="brand__mark"></span>Brightleaf</div>
    <span class="portal-link portal-link--resellers">Resellers Portal</span>
    <span class="portal-link portal-link--customer">Customer portal</span>
    <svg class="menu-toggle" width="12" height="9" viewBox="0 0 12 9"><g fill="#111"><rect width="12" height="1.5"/><rect y="3.7" width="12" height="1.5"/><rect y="7.4" width="12" height="1.5"/></g></svg>
  </header>
  <div class="hero">
    <div class="hero__photo hero__photo--split" role="img" aria-label="Split photo: solar panels on a roof and a gloved hand clearing leaves from a gutter"></div>
    <div class="hero__panel">
      <h1 class="hero__title">Australia’s Trusted Solar and Gutter Experts</h1>
      <div class="hero__choices">
        <span class="choice choice--solar">Solar Panel Cleaning</span>
        <span class="choice choice--gutter">Gutter Cleaning</span>
      </div>
    </div>
  </div>
  <footer class="site-footer">
    <div class="footer-brand"><span class="footer-brand__mark"></span><span class="footer-brand__name">Brightleaf</span></div>
    <span class="footer-rule footer-rule--one"></span>
    <div class="footer-col footer-col--locations">
      <h2 class="footer-col__heading">Location</h2>
      <ul class="footer-list">
        <li><svg width="4" height="3" viewBox="0 0 4 3"><path d="M0 0l1.5 1.5L0 3M2 0l1.5 1.5L2 3" stroke="#fff" stroke-width=".6" fill="none"/></svg>Sydney – 02 7391 8056</li>
        <li><svg width="4" height="3" viewBox="0 0 4 3"><path d="M0 0l1.5 1.5L0 3M2 0l1.5 1.5L2 3" stroke="#fff" stroke-width=".6" fill="none"/></svg>Southern Highlands – 02 4863 1708</li>
        <li><svg width="4" height="3" viewBox="0 0 4 3"><path d="M0 0l1.5 1.5L0 3M2 0l1.5 1.5L2 3" stroke="#fff" stroke-width=".6" fill="none"/></svg>Goulburn – 02 4863 1708</li>
        <li><svg width="4" height="3" viewBox="0 0 4 3"><path d="M0 0l1.5 1.5L0 3M2 0l1.5 1.5L2 3" stroke="#fff" stroke-width=".6" fill="none"/></svg>Canberra – 02 6172 4385</li>
        <li><svg width="4" height="3" viewBox="0 0 4 3"><path d="M0 0l1.5 1.5L0 3M2 0l1.5 1.5L2 3" stroke="#fff" stroke-width=".6" fill="none"/></svg>Wollongong – 02 4239 5817</li>
      </ul>
    </div>
    <span class="footer-rule footer-rule--two"></span>
    <div class="footer-col footer-col--company">
      <h2 class="footer-col__heading">Company Info</h2>
      <ul class="footer-list footer-list--company">
        <li><svg width="5" height="4" viewBox="0 0 5 4"><rect width="5" height="4" fill="#fff"/><path d="M0 0l2.5 2L5 0" stroke="#0a67b1" stroke-width=".5" fill="none"/></svg>sales@brightleaf.com.au</li>
        <li><svg width="5" height="4" viewBox="0 0 5 4"><path d="M0 .6l1.6-.6 1.8.6L5 0v3.4l-1.6.6-1.8-.6L0 4z" fill="#fff"/></svg><span>Head Office - Fernbrook NSW 2584<br>ABN: 48093716552</span></li>
      </ul>
    </div>
    <p class="copyright">© 2025 Brightleaf.&nbsp; All rights reserved.</p>
  </footer>
</section>

<!-- Screen 2: solar sectors -->
<section class="screen screen--solar">
  <header class="site-header">
    <div class="brand"><span class="brand__mark"></span>Brightleaf</div>
    <span class="portal-link portal-link--resellers">Resellers Portal</span>
    <span class="portal-link portal-link--customer">Customer portal</span>
    <svg class="menu-toggle" width="12" height="9" viewBox="0 0 12 9"><g fill="#111"><rect width="12" height="1.5"/><rect y="3.7" width="12" height="1.5"/><rect y="7.4" width="12" height="1.5"/></g></svg>
  </header>
  <div class="hero">
    <div class="hero__photo hero__photo--panels" role="img" aria-label="Photo of a brush pole cleaning a large solar panel array"></div>
    <div class="hero__panel">
      <h1 class="hero__title">Keep Your Solar Panels Clean and Efficient</h1>
      <p class="hero__sectors">Government – Infrastructure – Commercial – Residential</p>
    </div>
  </div>
  <footer class="site-footer">
    <div class="footer-brand"><span class="footer-brand__mark"></span><span class="footer-brand__name">Brightleaf</span></div>
    <span class="footer-rule footer-rule--one"></span>
    <div class="footer-col footer-col--locations">
      <h2 class="footer-col__heading">Location</h2>
      <ul class="footer-list">
        <li><svg width="4" height="3" viewBox="0 0 4 3"><path d="M0 0l1.5 1.5L0 3M2 0l1.5 1.5L2 3" stroke="#fff" stroke-width=".6" fill="none"/></svg>Sydney – 02 7391 8056</li>
        <li><svg width="4" height="3" viewBox="0 0 4 3"><path d="M0 0l1.5 1.5L0 3M2 0l1.5 1.5L2 3" stroke="#fff" stroke-width=".6" fill="none"/></svg>Southern Highlands – 02 4863 1708</li>
        <li><svg width="4" height="3" viewBox="0 0 4 3"><path d="M0 0l1.5 1.5L0 3M2 0l1.5 1.5L2 3" stroke="#fff" stroke-width=".6" fill="none"/></svg>Goulburn – 02 4863 1708</li>
        <li><svg width="4" height="3" viewBox="0 0 4 3"><path d="M0 0l1.5 1.5L0 3M2 0l1.5 1.5L2 3" stroke="#fff" stroke-width=".6" fill="none"/></svg>Canberra – 02 6172 4385</li>
        <li><svg width="4" height="3" viewBox="0 0 4 3"><path d="M0 0l1.5 1.5L0 3M2 0l1.5 1.5L2 3" stroke="#fff" stroke-width=".6" fill="none"/></svg>Wollongong – 02 4239 5817</li>
      </ul>
    </div>
    <span class="footer-rule footer-rule--two"></span>
    <div class="footer-col footer-col--company">
      <h2 class="footer-col__heading">Company Info</h2>
      <ul class="footer-list footer-list--company">
        <li><svg width="5" height="4" viewBox="0 0 5 4"><rect width="5" height="4" fill="#fff"/><path d="M0 0l2.5 2L5 0" stroke="#0a67b1" stroke-width=".5" fill="none"/></svg>sales@brightleaf.com.au</li>
        <li><svg width="5" height="4" viewBox="0 0 5 4"><path d="M0 .6l1.6-.6 1.8.6L5 0v3.4l-1.6.6-1.8-.6L0 4z" fill="#fff"/></svg><span>Head Office - Fernbrook NSW 2584<br>ABN: 48093716552</span></li>
      </ul>
    </div>
    <p class="copyright">© 2025 Brightleaf.&nbsp; All rights reserved.</p>
  </footer>
</section>

<!-- Screen 3: gutter sectors -->
<section class="screen screen--gutter">
  <header class="site-header">
    <div class="brand"><span class="brand__mark"></span>Brightleaf</div>
    <span class="portal-link portal-link--resellers">Resellers Portal</span>
    <span class="portal-link portal-link--customer">Customer portal</span>
    <svg class="menu-toggle" width="12" height="9" viewBox="0 0 12 9"><g fill="#111"><rect width="12" height="1.5"/><rect y="3.7" width="12" height="1.5"/><rect y="7.4" width="12" height="1.5"/></g></svg>
  </header>
  <div class="hero">
    <div class="hero__photo hero__photo--gutter" role="img" aria-label="Photo of a worker on a ladder cleaning a roof gutter"></div>
    <div class="hero__panel">
      <h1 class="hero__title">Protect Your Home with Gutter Cleaning</h1>
      <p class="hero__sectors">Government – Strata – Commercial – Residential</p>
    </div>
  </div>
  <footer class="site-footer">
    <div class="footer-brand"><span class="footer-brand__mark"></span><span class="footer-brand__name">Brightleaf</span></div>
    <span class="footer-rule footer-rule--one"></span>
    <div class="footer-col footer-col--locations">
      <h2 class="footer-col__heading">Location</h2>
      <ul class="footer-list">
        <li><svg width="4" height="3" viewBox="0 0 4 3"><path d="M0 0l1.5 1.5L0 3M2 0l1.5 1.5L2 3" stroke="#fff" stroke-width=".6" fill="none"/></svg>Sydney – 02 7391 8056</li>
        <li><svg width="4" height="3" viewBox="0 0 4 3"><path d="M0 0l1.5 1.5L0 3M2 0l1.5 1.5L2 3" stroke="#fff" stroke-width=".6" fill="none"/></svg>Southern Highlands – 02 4863 1708</li>
        <li><svg width="4" height="3" viewBox="0 0 4 3"><path d="M0 0l1.5 1.5L0 3M2 0l1.5 1.5L2 3" stroke="#fff" stroke-width=".6" fill="none"/></svg>Goulburn – 02 4863 1708</li>
        <li><svg width="4" height="3" viewBox="0 0 4 3"><path d="M0 0l1.5 1.5L0 3M2 0l1.5 1.5L2 3" stroke="#fff" stroke-width=".6" fill="none"/></svg>Canberra – 02 6172 4385</li>
        <li><svg width="4" height="3" viewBox="0 0 4 3"><path d="M0 0l1.5 1.5L0 3M2 0l1.5 1.5L2 3" stroke="#fff" stroke-width=".6" fill="none"/></svg>Wollongong – 02 4239 5817</li>
      </ul>
    </div>
    <span class="footer-rule footer-rule--two"></span>
    <div class="footer-col footer-col--company">
      <h2 class="footer-col__heading">Company Info</h2>
      <ul class="footer-list footer-list--company">
        <li><svg width="5" height="4" viewBox="0 0 5 4"><rect width="5" height="4" fill="#fff"/><path d="M0 0l2.5 2L5 0" stroke="#0a67b1" stroke-width=".5" fill="none"/></svg>sales@brightleaf.com.au</li>
        <li><svg width="5" height="4" viewBox="0 0 5 4"><path d="M0 .6l1.6-.6 1.8.6L5 0v3.4l-1.6.6-1.8-.6L0 4z" fill="#fff"/></svg><span>Head Office - Fernbrook NSW 2584<br>ABN: 48093716552</span></li>
      </ul>
    </div>
    <p class="copyright">© 2025 Brightleaf.&nbsp; All rights reserved.</p>
  </footer>
</section>

</body>
</html>
```